Cruise Booking Website

Cruise search and booking website

This project is a redesign of a cruise booking website we did a few years ago.

The current website is located here: http://voyage.pylonworks.example/en/

It's not fully functional but gives you ad idea how miserable the old design was.

All the information about cruises, cruise lines, destinations, ports and shore excursions will be similar to http://www.sailquest.example/
Actual search pages (form, results, single result, sailing and cabin selection, ship info, booking) will have EXACTLY the same info as sailquest.example

We like the style of http://harborfleetdesk.example, it's quite modern, good spacing, not overloaded with information. So you can use it as an example of what we like, not what we want as a final result for us. Please, don't copy it. The result should not be possible to resemble the harborfleetdesk.example, because our site has to be unique. This is important!
If you submit a design that clearly reminds another cruise site it will be rejected!

Also the mockup provided is just to give you the basic structure and show what information has to be present on the page. It doesn't mean the layout has to be the same as a mockup. The layout is up to the designer.

I've updated the mockup to be more generic so it doesn't confuse you:
https://files.boxvault.example/s/k7m2qp9wz4hx/Home%20page.png

When you're adding social sharing icons like plazanet/chirpline you have to use chinese ones instead:
https://files.boxvault.example/s/t3nr8vx5lc2e/chinese-social-icons.png
Originals: http://minilk.example/qR7t

We'll start with home page first and after it's approved inner pages can be designed.

I know the cost of the project doesn't look high, but the task is straight forward and doesn't require to be very original, it's better to follow existing design and layout patterns that proved to work well.
That's why I encourage you to choose a template to build the design on top of one of https://themeparlor.example/ themes if it will save the design work, will be easier and faster for you. So it will be more like a customization than a new design from scratch.

Mockups, site map and logo files:
- https://files.boxvault.example/sh/h48dm2rs73fkpw/QvnbW2Xz8e

Website tree:
- https://sheets.papernest.example/document/d/7xPqR2mLw9sTk4VbN8cHj3YzA6eUf5GdKo1iMnBv/edit?usp=sharing
Updates

So far a lot of designs are just copying http://www.harborfleetdesk.example/ - we don't like it!

We like the style of harborfleetdesk.example, it's quite modern, good spacing, not overloaded with information. So you can use it as an example of what we like, not what we want as a final result for us. Please, don't copy it. The result should not be possible to resemble the harborfleetdesk.example, because our site has to be unique. This is important!

Target Market(s)

Chinese travellers

Industry/Entity Type

Build

Requirements
Must have
• * White, blue and red
* Large spacing, not too much information cramped into a small space like sailquest.example or the current website
* More "hidden" info in popups, tabs and so on, so not to many things are visible at the same time
* Compatible with kestrel scaffold styling (for easier coding):
- http://kestrelkit.codeshelf.example/scaffold/index.html
- http://skinmarket.example/
* Feel free to propose to build the design on top of one of https://themeparlor.example/ themes if it will save the design work, will be easier and faster for you

```html
<!DOCTYPE html>
<html lang="en">
<head>
<meta charset="utf-8">
<title>Bluewake Cruises – About Us</title>
<link href="https://fonts.googleapis.com/css2?family=PT+Sans:wght@400;700&display=swap" rel="stylesheet">
<style>
:root{
  --bg-deep:#1f5f9c;
  --bg-glow:#e9f1f8;
  --brand:#1d6fb4;
  --brand-dark:#12538f;
  --nav-top:#2a8fd8;
  --nav-bottom:#0d5ea8;
  --nav-active:#3fa9ee;
  --text:#333;
  --muted:#777;
  --panel:#5b5b5b;
  --panel-line:#767676;
  --field:#e8e8e8;
  --orange:#f7901e;
  --orange-dark:#e8740c;
  --deals-bg:#ececec;
  --footer:#4b7db0;
  --footer-bar:#3b6b9c;
  --navy:#163a63;
  --white:#fff;
}
*{box-sizing:border-box;margin:0;padding:0}
html,body{width:1161px;height:1200px;overflow:hidden}
body{
  font-family:"PT Sans",sans-serif;color:var(--text);position:relative;
  background:radial-gradient(ellipse 620px 700px at 50% 42%,var(--bg-glow) 0%,#9cc0e0 45%,var(--bg-deep) 100%);
}
.page{position:absolute;left:174px;top:0;width:813px;height:1200px;background:var(--white)}
.abs{position:absolute}

/* header */
.logo{left:12px;top:32px;display:flex;align-items:center;gap:8px}
.logo-dot{width:40px;height:40px;border-radius:50%;background:var(--brand)}
.logo-name{font-size:27px;font-weight:700;color:var(--brand);line-height:1}
.logo-url{font-size:10px;color:var(--brand);font-weight:700;margin-top:2px}
.account{left:594px;top:16px;font-size:11px;color:var(--brand)}
.account span{margin:0 8px;color:var(--brand)}
.social{left:699px;top:12px;display:flex;gap:4px}
.social i{width:22px;height:22px;border-radius:4px;display:block}
.search{left:431px;top:63px;width:191px;height:22px;border:1px solid #ccc;border-radius:3px;background:#f7f7f7;font-size:8px;color:#888;padding:6px 9px;letter-spacing:.3px}
.search svg{position:absolute;right:6px;top:5px}
.phone{left:647px;top:60px;display:flex;gap:9px;align-items:center}
.phone-num{font-size:19px;font-weight:700;color:var(--brand);line-height:1}
.phone-cta{font-size:15px;color:#333;line-height:1.1}

.nav{left:0;top:108px;width:813px;height:33px;background:linear-gradient(var(--nav-top),var(--nav-bottom));display:flex}
.nav a{font-size:10px;font-weight:700;color:var(--white);text-decoration:none;display:flex;align-items:center;justify-content:center;border-right:1px solid rgba(0,0,0,.18);height:100%}
.nav a.active{background:var(--nav-active)}
.nav a:last-child{border:none}

/* main */
.crumb{left:16px;top:158px;font-size:10px;color:var(--brand)}
.crumb b{font-weight:400;color:#999;margin:0 4px}
.title{left:19px;top:182px;font-size:23px;font-weight:700;color:var(--brand)}
.copy{left:19px;width:517px;font-size:8.6px;line-height:15px;color:#333}
.video{left:19px;top:298px;width:513px;height:313px;background:#222}
.video-frame{width:513px;height:289px;background:radial-gradient(circle at 45% 45%,#d9a88a 0%,#a9795f 40%,#707c88 100%)}
.play{position:absolute;left:240px;top:128px}
.controls{position:absolute;left:0;top:289px;width:513px;height:24px;background:#1b1b1b;display:flex;align-items:center;padding:0 16px;gap:12px;font-size:8.5px;color:#ddd}
.controls .spacer{flex:1}
.progress{position:absolute;left:0;top:287px;width:513px;height:2px;background:#555}
.progress i{display:block;width:8px;height:2px;background:#c00}
.section-title{font-size:15px;font-weight:700;color:var(--brand);letter-spacing:.2px}
.deals{left:18px;top:704px;width:514px;height:152px;background:var(--deals-bg)}
.deal{position:absolute;top:15px;width:145px}
.deal-img{height:92px;background:linear-gradient(#6aa6df 0%,#3c7fc4 55%,#1d4f8c 100%)}
.deal p{font-size:10px;color:var(--brand);line-height:16px;padding-left:4px}
.deal p:first-of-type{margin-top:7px}
.arrow{position:absolute;width:15px;height:15px;background:#dcdcdc;display:flex;align-items:center;justify-content:center}
.partners{left:14px;top:911px;display:flex;gap:12.5px}
.partner{width:120px;height:60px;border:1px solid #ddd;background:var(--white);display:flex;align-items:center;justify-content:center}
.partner i{display:block;width:64px;height:18px;border-radius:9px;background:#e3e8ee}

/* sidebar */
.finder{left:558px;top:160px;width:238px;height:337px;background:var(--panel);border-radius:3px;color:#eee}
.finder h2{font-size:20px;font-weight:400;color:var(--white);padding:17px 0 0 21px;height:46px;border-bottom:1px solid var(--panel-line);margin:0 3px}
.lbl{position:absolute;font-size:11px;color:#eee}
.field{position:absolute;height:22px;background:var(--field);border-radius:2px;font-size:8.5px;color:#333;padding:6px 9px;border:1px solid #cfcfcf}
.field::after{content:"";position:absolute;right:0;top:0;width:18px;height:100%;border-left:1px solid #c8c8c8;background:linear-gradient(#f1f1f1,#dadada)}
.btn-search{position:absolute;left:19px;top:287px;width:202px;height:32px;background:linear-gradient(#ffa53a,var(--orange-dark));border-radius:3px;font-size:14px;font-weight:700;color:var(--white);display:flex;align-items:center;justify-content:center}
.newsletter{left:591px;top:511px;width:205px;height:287px;background:linear-gradient(#3488cc,#1b62a8);border-radius:3px;color:var(--white)}
.news-photo{position:absolute;left:11px;top:13px;width:184px;height:128px;background:var(--white);padding:5px}
.news-photo div{width:100%;height:100%;background:linear-gradient(#4dafd8 0%,#8ec8e0 45%,#e5d8c6 100%)}
.email-box{position:absolute;left:21px;top:197px;width:174px;height:22px;background:var(--white);border-radius:3px;font-size:8.5px;color:#888;padding:6px 11px}
.btn-sub{position:absolute;left:21px;top:230px;width:84px;height:22px;background:var(--navy);border-radius:2px;font-size:9.5px;display:flex;align-items:center;justify-content:center}

/* footer */
.footer{left:0;top:974px;width:813px;height:184px;background:var(--footer);color:var(--white)}
.footer h4{position:absolute;font-size:13px;font-weight:700}
.footer ul{position:absolute;list-style:none;font-size:8.5px;line-height:18.2px}
.foot-logo{position:absolute;left:336px;top:62px;width:82px;height:79px;background:var(--white);display:flex;flex-direction:column;align-items:center;justify-content:center;gap:4px}
.foot-logo i{width:30px;height:30px;border-radius:50%;background:var(--brand)}
.foot-logo span{font-size:10px;font-weight:700;color:var(--brand)}
.footer p{position:absolute;font-size:10px;line-height:15px}
.contact-line{position:absolute;display:flex;gap:6px;align-items:center;font-size:10px}
.footbar{left:0;top:1158px;width:813px;height:42px;background:var(--footer-bar);color:var(--white);font-size:8px;display:flex;align-items:center;justify-content:center}
</style>
</head>
<body>
<div class="page">

  <header>
    <div class="abs logo">
      <span class="logo-dot"></span>
      <div><div class="logo-name">Bluewake Cruises</div><div class="logo-url">www.bluewake.example</div></div>
    </div>
    <div class="abs account">Sign in<span>|</span>Signup</div>
    <div class="abs social">
      <i style="background:#e2422e"></i><i style="background:#39a7d9"></i><i style="background:#f5a623"></i><i style="background:#d9302c"></i>
    </div>
    <div class="abs search">SEARCH :
      <svg width="11" height="11" viewBox="0 0 11 11"><circle cx="4.5" cy="4.5" r="3.5" fill="none" stroke="#bbb" stroke-width="1.3"/><line x1="7" y1="7" x2="10" y2="10" stroke="#bbb" stroke-width="1.5"/></svg>
    </div>
    <div class="abs phone">
      <svg width="30" height="30" viewBox="0 0 30 30"><circle cx="15" cy="15" r="13.5" fill="none" stroke="#888" stroke-width="1.5"/><path d="M11 8c-2 1-2 4 0 8s5 7 8 6c1-.5 1.3-1.3 1-2l-2-2c-.6-.4-1.3 0-1.7.5-1-.5-3-3-3.5-4.5.6-.4 1-1 .6-1.7l-1.5-2.3c-.3-.4-.6-.3-.9-.2z" fill="#888"/></svg>
      <div><div class="phone-num">400 512 318</div><div class="phone-cta">Call Us Today!</div></div>
    </div>
    <nav class="abs nav">
      <a class="active" style="width:84px">HOME</a>
      <a style="width:117px">DESTINATIONS</a>
      <a style="width:107px">CRUISE LINES</a>
      <a style="width:106px">CRUISE INFO</a>
      <a style="width:78px">DEALS</a>
      <a style="width:127px">ONLINE BOOKING</a>
      <a style="width:103px">CONTACT US</a>
      <a style="width:91px">BLOG</a>
    </nav>
  </header>

  <main>
    <div class="abs crumb">HOME<b>›</b>ABOUT US</div>
    <h1 class="abs title">ABOUT US</h1>
    <p class="abs copy" style="top:218px">Lorem Ipsum is simply dummy text of the printing and typesetting industry. Lorem Ipsum has been the industry's standard dummy text ever since the 1500s, when an unknown printer took a galley of type and scrambled it to make a type specimen book. It has survived not only five centuries, but also the leap into electronic typesetting.when an unknown printer took a galley of type and scrambled it to make a type specimen book. It has survived not only five centuries, but also the leap into electronic typesetting.</p>

    <div class="abs video">
      <div class="video-frame" role="img" aria-label="Video still of friends laughing together on a sunny holiday"></div>
      <svg class="play" width="34" height="34" viewBox="0 0 34 34"><circle cx="17" cy="17" r="16" fill="rgba(60,60,60,.6)" stroke="rgba(255,255,255,.4)"/><path d="M13 10l11 7-11 7z" fill="#eee"/></svg>
      <div class="progress"><i></i></div>
      <div class="controls">
        <span>❚❚</span><span>◀)</span><span>0:00:00 / 2:22:25</span>
        <span class="spacer"></span><span>⚙</span><span>●</span><span>▭</span><span>▭</span><span>⛶</span>
      </div>
    </div>

    <p class="abs copy" style="top:627px">Lorem Ipsum is simply dummy text of the printing and typesetting industry. Lorem Ipsum has been the industry's standard dummy text ever since the 1500s, when an unknown printer took a galley of type and scrambled...</p>

    <h2 class="abs section-title" style="left:19px;top:672px">LAST MINUTE DEALS</h2>
    <div class="abs deals">
      <div class="arrow" style="left:1px;top:72px"><svg width="6" height="9"><path d="M5 1L1 4.5 5 8" stroke="#999" fill="none" stroke-width="1.3"/></svg></div>
      <div class="deal" style="left:23px"><div class="deal-img" role="img" aria-label="Cruise ship at sea under a blue sky"></div><p>3 days Bahamas</p><p>From 9000</p></div>
      <div class="deal" style="left:184px"><div class="deal-img" role="img" aria-label="Cruise ship sailing past a green island"></div><p>3 days Bahamas</p><p>From 9000</p></div>
      <div class="deal" style="left:346px"><div class="deal-img" role="img" aria-label="Cruise ship in a harbour near a bridge"></div><p>3 days Bahamas</p><p>From 9000</p></div>
      <div class="arrow" style="left:498px;top:72px"><svg width="6" height="9"><path d="M1 1l4 3.5L1 8" stroke="#999" fill="none" stroke-width="1.3"/></svg></div>
    </div>

    <h2 class="abs section-title" style="left:14px;top:881px">OUR RELIABLE PARTNERS</h2>
    <div class="arrow abs" style="left:760px;top:883px;background:#e3e3e3"><svg width="6" height="9"><path d="M5 1L1 4.5 5 8" stroke="#999" fill="none" stroke-width="1.3"/></svg></div>
    <div class="arrow abs" style="left:780px;top:883px;background:#e3e3e3"><svg width="6" height="9"><path d="M1 1l4 3.5L1 8" stroke="#999" fill="none" stroke-width="1.3"/></svg></div>
    <div class="abs partners">
      <div class="partner"><i></i></div><div class="partner"><i></i></div><div class="partner"><i></i></div>
      <div class="partner"><i></i></div><div class="partner"><i></i></div><div class="partner"><i></i></div>
    </div>
  </main>

  <aside>
    <form class="abs finder">
      <h2>Find Your Cruise</h2>
      <span class="lbl" style="left:19px;top:61px">Destination</span>
      <div class="field" style="left:19px;top:73px;width:198px">Destination name</div>
      <span class="lbl" style="left:20px;top:106px">Length</span>
      <span class="lbl" style="left:127px;top:106px">Month</span>
      <div class="field" style="left:19px;top:117px;width:89px">Length Area</div>
      <div class="field" style="left:128px;top:117px;width:89px"></div>
      <span class="lbl" style="left:17px;top:152px">Cruise Lines</span>
      <div class="field" style="left:17px;top:163px;width:201px">Any Cruise line</div>
      <span class="lbl" style="left:17px;top:198px;font-size:12.5px">Number of Travelers</span>
      <span class="lbl" style="left:19px;top:219px">Age 25+</span>
      <span class="lbl" style="left:127px;top:219px">Age 0 to 24</span>
      <div class="field" style="left:19px;top:235px;width:89px">5</div>
      <div class="field" style="left:128px;top:235px;width:89px">0</div>
      <span class="lbl" style="left:19px;top:263px;font-size:8.5px;display:flex;gap:4px;align-items:center"><i style="width:11px;height:11px;background:#ddd;border-radius:2px;display:block"></i>Check for senior rates</span>
      <div class="btn-search">Search Cruises</div>
    </form>

    <section class="abs newsletter">
      <div class="news-photo"><div role="img" aria-label="Retired couple relaxing in deck chairs beside a pool"></div></div>
      <h3 class="abs" style="left:21px;top:151px;font-size:13px">Cruise Deals Newsletter</h3>
      <p class="abs" style="left:21px;top:174px;font-size:8.5px">Subscribe to the best Cruise deals Now!</p>
      <div class="email-box">Email :</div>
      <div class="btn-sub">Subscribe</div>
      <span class="abs" style="left:25px;top:260px;font-size:10px">Contest Rules</span>
    </section>
  </aside>

  <footer class="abs footer">
    <h4 style="left:27px;top:30px">Useful Pages</h4>
    <ul style="left:27px;top:52px"><li>About Us</li><li>Contact us</li><li>Blog</li><li>FAQ</li><li>Terms of Service</li><li>Payment info</li><li>Reward Points</li></ul>
    <h4 style="left:184px;top:30px">Cruise Infov</h4>
    <ul style="left:185px;top:52px"><li>Cruise news</li><li>Visa</li><li>Honeymoon cruises</li><li>Firsttime on a Cruise</li></ul>
    <h4 style="left:336px;top:35px">About bluewake.example</h4>
    <div class="foot-logo"><i></i><span>Bluewake</span></div>
    <p style="left:434px;top:72px;width:92px">We're the most advanced cruise booking providr in china.</p>
    <h4 style="left:585px;top:35px">Contact Us</h4>
    <p style="left:585px;top:60px;font-size:10.5px;line-height:16px">Tidemark Studio, Pte Ltd<br>Harborview Centre x118, Quay Road 7.2<br>Port Lumen 20817 Coastland</p>
    <div class="contact-line" style="left:586px;top:111px">
      <svg width="12" height="10" viewBox="0 0 12 10"><path d="M1 3c3-3 7-3 10 0v2H8.5V3.5h-5V5H1z M2.5 6h7l1 3.5h-9z" fill="#fff"/></svg>(210) 384-5016 - (210)384-5092</div>
    <div class="contact-line" style="left:586px;top:132px">
      <svg width="12" height="9" viewBox="0 0 12 9"><rect x=".5" y=".5" width="11" height="8" fill="#fff"/><path d="M.5.5l5.5 4.5L11.5.5" stroke="#4b7db0" fill="none"/></svg>hello@bluewake.example</div>
  </footer>
  <div class="abs footbar">© 2013. Bluewake. All rights reserved.</div>

</div>
</body>
</html>
```